BUSINESS CARD - HALLORAN FIELD SERVICES

I would like to create a business card for my fertilizer spreading business. I would like to incorporate my existing logo and also a description of the services offered. The business card will be given to farmers so must be kept simple but effective. It will also be left in stores so much also be eye catching in order to stand out from other cards.

Target Market(s)

FARMERS

Requirements
Must have
• FRONT OF CARD = EXISTING LOGO + "CUSTOMISED SPREADING" below the logo

REAR Of CARD = SERVICES OFFERED AND CONTACT DETAILS

- Bulk fertilizer including Lime, Gypsum, Manure & Compost
- Granular fertilizer including Single Super, Urea, Gran-am, & Custom Blends
- Modern equipment - Autosteer & Variable Rate Capable
- Friendly & Reliable Service
- Contact Gus: 0417 552 308
Nice to have
• utilize same color scheme as existing logo

```html
<!DOCTYPE html>
<html lang="en">
<head>
<meta charset="utf-8">
<title>Halloran Field Services – Business Card</title>
<link rel="stylesheet" href="https://fonts.googleapis.com/css2?family=Arimo:wght@400;700&display=swap">
<style>
  :root {
    --backdrop: #0d0d0d;
    --card: #2b2b2d;
    --card-edge: #f39420;
    --ink-grey: #8a8a8d;
    --ink-light: #c9c9cb;
    --accent: #f39420;
    --emboss: #3a3a3d;
  }
  * { box-sizing: border-box; margin: 0; padding: 0; }
  html, body {
    width: 1200px; height: 820px; overflow: hidden;
    background: var(--backdrop);
    font-family: "Arimo", Arial, sans-serif;
  }
  .sheet {
    width: 1200px; height: 820px;
    display: flex; align-items: center; justify-content: center; gap: 40px;
  }
  .card {
    position: relative;
    width: 540px; height: 309px;
    background: var(--card);
    border-bottom: 3px solid var(--card-edge);
    border-right: 3px solid var(--card-edge);
    overflow: hidden;
  }

  /* Rear of card */
  .card-rear .brand {
    position: absolute; right: 40px; top: 34px;
    display: flex; align-items: center; gap: 14px;
  }
  .brand-disc {
    width: 44px; height: 44px; border-radius: 50%;
    background: var(--ink-grey);
  }
  .brand-name {
    font-weight: 700; font-size: 21px; color: var(--ink-grey);
    letter-spacing: -0.3px;
  }
  .services {
    position: absolute; left: 36px; bottom: 34px;
    list-style: none;
    font-size: 13px; line-height: 16px; color: var(--ink-grey);
  }
  .services li { position: relative; padding-left: 16px; margin-top: 4px; }
  .services li::before {
    content: ""; position: absolute; left: 0; top: 4px;
    width: 8px; height: 8px; border-radius: 50%; background: var(--accent);
  }
  .contact {
    position: absolute; right: 40px; bottom: 96px; text-align: right;
    color: var(--ink-grey);
  }
  .contact-label { font-size: 17px; }
  .contact-line { font-size: 19px; margin-top: 4px; }
  .contact-phone { color: var(--accent); }

  /* Front of card */
  .card-front .front-disc {
    position: absolute; left: 60px; top: 42px;
    width: 225px; height: 225px; border-radius: 50%;
    background: var(--emboss);
  }
  .card-front .front-brand {
    position: absolute; right: 34px; top: 124px; text-align: right;
  }
  .front-brand .brand-name { font-size: 20px; }
  .tagline {
    margin-top: 10px; font-size: 11px; letter-spacing: 0.6px; color: var(--ink-light);
  }
</style>
</head>
<body>
  <main class="sheet">
    <section class="card card-rear" aria-label="Rear of card">
      <div class="brand">
        <span class="brand-disc" aria-hidden="true"></span>
        <span class="brand-name">Halloran Field Services</span>
      </div>
      <ul class="services">
        <li>Bulk fertilizer including Lime<br>Gypsum, Manure &amp; Compost</li>
        <li>Granular fertilizer including Single<br>Super, Urea, Gran-am, &amp; Custom Blends</li>
        <li>Modern equipment</li>
        <li>Autosteer &amp; Variable Rate Capable</li>
        <li>Friendly &amp; Reliable Service</li>
      </ul>
      <div class="contact">
        <p class="contact-label">Contact</p>
        <p class="contact-line">Gus: <span class="contact-phone">0417 552 308</span></p>
      </div>
    </section>

    <section class="card card-front" aria-label="Front of card">
      <span class="front-disc" aria-hidden="true"></span>
      <div class="front-brand">
        <p class="brand-name">Halloran Field Services</p>
        <p class="tagline">CUSTOMISED SPREADING</p>
      </div>
    </section>
  </main>
</body>
</html>
```